HVAC Design Services

I want a brochure to market my services. I own TOVEN Design Services LLC. I specialize in Mechanical Design with HVAC Design being my
specialty. I also do Plumbing and Civil Design. I have a strong resume with over 30 years experience. I was the Lead Mechanical Designer and Cad Manager for the mechanical group at an Architectural Engineering company for over 10 years.

I would like a professional looking brochure to pass out to engineering offices. I am targeting over-load work, when an office is so busy they need temporary help. Special project. Freeing up the engineer with my experience and capability to work with little to no direction .

1. HVAC Design
a) Calculate cfm
b) Layout and route ductwork
c) Size Ductwork
d) Choose and Layout grilles, registers and diffusers
e) Choose equipment and locate on plans
f) Create HVAC Floor Plans, Sections, Details and Schedules

2. Plumbing Design
a) Layout and route plumbing
b) Size piping
c) Create Plumbing Floor Plans, Sections, Details and Schedules.

3. AutoCAD 3D Modeling

4. Civil and GIS experience

5. AutoCAD 3D Modeling

6. Some Electrical and Structural Design experience

```html
<!DOCTYPE html>
<html lang="en">
<head>
<meta charset="UTF-8">
<title>TOVEN Design Services LLC – Over-loaded? Get a hand</title>
<link rel="stylesheet" href="https://fonts.googleapis.com/css2?family=Bebas+Neue&display=swap">
<style>
  :root{
    --paper:#ffffff;
    --ink-grey:#333333;
    --navy:#0f2240;
    --green-deep:#3f7f2f;
    --green:#5fa548;
    --green-light:#7dbf5f;
    --concrete:#c9c9c9;
    --concrete-dark:#8e8e8e;
    --brick:#b8806a;
    --stripe-grey:#d6d6d8;
    --teal:#1f9fa0;
  }
  *{margin:0;padding:0;box-sizing:border-box}
  html,body{width:1200px;height:927px;overflow:hidden;background:var(--paper)}
  .brochure{position:relative;width:1200px;height:927px;overflow:hidden;background:var(--paper);
    font-family:"Bebas Neue",Impact,sans-serif;}
  .backdrop{position:absolute;inset:0;width:1200px;height:927px}
  .headline-box{position:absolute;left:831px;top:140px;width:326px;height:144px;
    border:2px solid var(--paper);color:var(--paper);display:flex;flex-direction:column;
    justify-content:center;align-items:center;font-size:50px;line-height:48px;letter-spacing:.5px}
  .experience{position:absolute;left:30px;top:408px;width:354px;text-align:center;
    color:var(--ink-grey);font-size:47px;line-height:45px}
  .contact{position:absolute;left:447px;top:558px;width:310px;text-align:center;color:var(--navy)}
  .contact-name{font-size:47px;line-height:50px}
  .contact-phone{display:inline-block;margin-top:2px;width:269px;height:60px;background:var(--navy);
    color:var(--paper);font-size:47px;line-height:62px}
  .contact-role{margin-top:9px;font-size:33px;line-height:31px}
  .company{position:absolute;left:862px;top:790px;width:270px;color:var(--ink-grey);
    display:flex;align-items:center;gap:14px}
  .company-mark{width:22px;height:22px;background:var(--ink-grey);flex:none}
  .company-name{font-size:44px;line-height:42px}
  .company-name span{display:block;font-size:26px;line-height:28px;letter-spacing:3px}
</style>
</head>
<body>
<main class="brochure">
  <svg class="backdrop" viewBox="0 0 1651 1277" preserveAspectRatio="none" aria-hidden="false">
    <defs>
      <linearGradient id="facadeTone" x1="0" y1="0" x2="1" y2="1">
        <stop offset="0" stop-color="#e6e6e6"/>
        <stop offset=".55" stop-color="#9a9a9a"/>
        <stop offset="1" stop-color="#b8806a"/>
      </linearGradient>
      <linearGradient id="timberTone" x1="0" y1="0" x2="1" y2="1">
        <stop offset="0" stop-color="#2f6a24"/>
        <stop offset=".5" stop-color="#4d9a3c"/>
        <stop offset="1" stop-color="#6fb653"/>
      </linearGradient>
      <linearGradient id="circuitTone" x1="0" y1="0" x2="1" y2="1">
        <stop offset="0" stop-color="#6fb653"/>
        <stop offset="1" stop-color="#3f7f2f"/>
      </linearGradient>
    </defs>
    <g class="photo-facade" role="img" aria-label="Photo of a modern building facade with metal balconies, windows and brick">
      <polygon points="0,0 1651,0 1651,770 1440,930 0,175" fill="url(#facadeTone)"/>
    </g>
    <g class="photo-stair" role="img" aria-label="Green-tinted photo of a spiral staircase beside timber-clad walls">
      <polygon points="70,0 1651,0 1651,590 1505,755" fill="url(#timberTone)"/>
    </g>
    <polygon class="stripe-grey" points="0,845 0,870 790,1277 840,1277" fill="var(--stripe-grey)"/>
    <g class="photo-circuit" role="img" aria-label="Green-tinted photo of an electronics breadboard with wires and relays">
      <polygon points="0,880 0,1277 790,1277" fill="url(#circuitTone)"/>
    </g>
    <polygon class="stripe-teal" points="455,1098 475,1098 832,1277 812,1277" fill="var(--teal)"/>
  </svg>

  <div class="headline-box">
    <span>Over-loaded?</span>
    <span>Get a hand</span>
  </div>

  <p class="experience">Some electrical<br>and structural<br>design experience</p>

  <section class="contact">
    <h1 class="contact-name">MARCO VANCE</h1>
    <div class="contact-phone">(509)-555-0142</div>
    <p class="contact-role">SR. Mechanical/Civil<br>Project Designer</p>
  </section>

  <div class="company">
    <div class="company-mark"></div>
    <div class="company-name">TOVEN DESIGN<span>SERVICES LLC</span></div>
  </div>
</main>
</body>
</html>
```